Trucking Company Website Design

We are working with a Trucking company in California. They provide trucking services for dirt, gravel, landscape bark, and landscape materials.

As you might imagine, there are no websites we could find for inspiration for trucking companies.

Thank you for taking the time to consider designing a website for us. We are web developers based in Stockton, CA, USA. Most of our projects go through the same process. Understanding this process may help you win a project with us. We custom-code all of our websites in-house. We don’t have any requirements as to what tools you use for your design, but we ask that you follow these guidelines.

IMAGES:
If you use any images or icons in the design, we ask that you have a link to the asset so we can purchase the image/icon. Most of the designs we submit do not have the customer’s images on them unless they have some great images. Be creative; show us the feeling you are trying to portray with your image choices. Use any royalty-free site you choose. We subscribe to Quillo and mainly use their images, but we can purchase images outside of Quillo. PLEASE NOTE: we will not submit designs to clients with watermarks on the images.

FONTS:
We ask that you identify the fonts you’re using in the design. This can be done in a message if you want. We typically use Varnex Fonts and Quillo Fonts.

CONTENT:
We're always open to different content and ideas. We often submit designs with stock images so the client can see our vision. We typically take pictures after the website launch to use their images with our vision. Lorem Ipsum is fine for paragraphs, but we ask that you make the Headers with correct English. We want to be able to show the vision and identify the sections of the website.

INSPIRATION:
We typically add a couple of links in the brief of websites we like to help you get started in your design.

REVISIONS:
We do not often ask for revisions of the designs unless we see something in the design that may not appeal to the client. If there are slight changes that we want to make, we do that in the development process.

FEEDBACK:
We rarely give feedback on designs during the design process. We are working on many website projects and do not have the time to provide feedback. We usually respond if your request is well thought out and asks specific questions, but a note asking “feedback, please” usually goes unanswered.

```html
<!DOCTYPE html>
<html lang="en">
<head>
<meta charset="UTF-8">
<title>Ridgeline Haulage — Trucking Services</title>
<link href="https://fonts.googleapis.com/css2?family=Saira:wght@700;800&family=Roboto:wght@400;500;700&display=swap" rel="stylesheet">
<style>
:root{
  --blue:#1a7fb8;
  --blue-dark:#0b6a8c;
  --teal-top:#3ab6d8;
  --red:#f03040;
  --red-dark:#dc2a22;
  --ink:#111;
  --gray:#666;
  --band:#6a6a6a;
  --footer:#000;
}
*{margin:0;padding:0;box-sizing:border-box}
html,body{width:1200px;height:2854px;overflow:hidden;background:#fff;font-family:'Roboto',sans-serif;color:var(--ink)}
.page{position:relative;width:1200px;height:2854px}
.abs{position:absolute}
.display{font-family:'Saira',sans-serif;font-weight:800;text-transform:uppercase}
.btn{position:absolute;display:flex;align-items:center;justify-content:center;color:#fff;font-weight:700;font-size:16px;background:linear-gradient(180deg,var(--red),var(--red-dark))}
.brand{font-family:'Roboto',sans-serif;font-weight:700;font-size:24px;color:var(--blue);display:flex;align-items:center;gap:10px;letter-spacing:.5px}
.brand-square{width:26px;height:26px;background:var(--red)}

/* header */
.header{top:0;left:0;width:1200px;height:107px;border-top:4px solid var(--blue);background:#fff}
.nav{top:72px;right:112px;display:flex;gap:58px;font-size:15px;color:#555}

/* hero */
.hero{top:107px;left:0;width:1200px;height:600px;overflow:hidden}
.hero-photo{position:absolute;inset:0;background:linear-gradient(100deg,#2a1838 0%,#4a2a4a 35%,#7a3a30 62%,#c86a20 78%,#3a2030 100%)}
.hero h1{top:130px;left:111px;font-size:72px;line-height:78px;color:#fff;text-transform:none}
.hero p{top:298px;left:111px;width:540px;font-size:18px;line-height:30px;color:#fff;font-weight:500}

/* section heads */
.sec-title{left:0;width:1200px;text-align:center;font-size:48px}
.sec-title span{color:var(--blue)}
.sec-text{left:190px;width:820px;text-align:center;font-size:14px;line-height:26px;color:var(--gray)}

/* service cards */
.card{top:970px;width:230px;height:275px;border-radius:6px;color:#fff;text-align:center}
.card.red{background:linear-gradient(180deg,#fb3352,#e02a24)}
.card.teal{background:linear-gradient(180deg,var(--teal-top),var(--blue-dark))}
.card .icon{position:absolute;top:31px;left:72px}
.card h3{position:absolute;top:145px;left:0;width:100%;font-size:17px;font-weight:800}
.card p{position:absolute;top:178px;left:25px;width:180px;font-size:12px;line-height:21.5px}

/* about */
.about-band{top:1426px;left:0;width:1200px;height:408px;background:linear-gradient(90deg,#707070,#5e5e5e)}
.about-truck{top:1348px;left:630px;width:570px;height:542px;background:radial-gradient(ellipse at 60% 55%,#2f5fbf 0%,#2a50a0 45%,rgba(120,130,150,.5) 70%,rgba(255,255,255,0) 78%)}
.about h2{top:1480px;left:111px;font-size:48px;color:#fff}
.about p{top:1553px;left:111px;width:430px;font-size:14px;line-height:25.7px;color:#fff}

/* contact */
.info{left:119px;display:flex;gap:14px}
.info .ring{width:50px;height:50px;border:2px solid var(--blue);border-radius:50%;display:flex;align-items:center;justify-content:center;flex:none}
.info h4{font-size:17px;font-weight:500;margin-top:2px}
.info div.txt{font-size:16px;line-height:26px;color:#555}
.field{position:absolute;background:#fff;box-shadow:0 0 18px rgba(0,0,0,.08);font-size:16px;color:#888;padding:16px 24px}

/* footer */
.footer{top:2552px;left:0;width:1200px;height:302px;background:var(--footer);color:#fff}
.footer-nav{top:155px;left:0;width:1200px;display:flex;justify-content:center;gap:70px;font-size:16px}
.social{top:205px;left:0;width:1200px;display:flex;justify-content:center;gap:12px}
.social span{width:30px;height:30px;border-radius:50%;background:#fff}
.copy{top:258px;left:0;width:1200px;text-align:center;font-size:12px}
</style>
</head>
<body>
<div class="page">

  <header class="abs header">
    <div class="abs brand" style="top:34px;left:110px"><span>RIDGELINE HAULAGE</span><span class="brand-square"></span></div>
    <div class="btn" style="top:12px;left:962px;width:126px;height:42px">Get Started</div>
    <nav class="abs nav"><span>Home</span><span>About Us</span><span>Our Services</span><span>Reviews</span><span>Contact Us</span></nav>
  </header>

  <section class="abs hero">
    <div class="hero-photo" role="img" aria-label="City skyline and suspension bridge at night"></div>
    <svg class="abs" style="top:96px;left:110px" width="290" height="390" viewBox="0 0 290 390">
      <polygon points="0,0 150,0 290,195 150,390 0,390 140,195" fill="#e8283c" opacity=".45"/>
    </svg>
    <h1 class="abs display">Welcome To<br>Ridgeline Haulage</h1>
    <p class="abs">Sed ut perspiciatis unde omnis iste natus error sit voluptatem accusantium doloremque laudantium, totam rem aperiam, eaque ipsa quae ab illo inventore veritatis et quasi</p>
    <div class="btn" style="top:418px;left:111px;width:127px;height:43px">Get Started</div>
  </section>

  <h2 class="abs display sec-title" style="top:796px">Our <span>Services</span></h2>
  <p class="abs sec-text" style="top:873px">Sed ut perspiciatis unde omnis iste natus error sit voluptatem accusantium doloremque laudantium, totam rem aperiam, eaque ipsa quae ab illo inventore veritatis et quasi architecto beatae vitae dicta sunt explicabo. Nemo enim ipsam voluptatem quia</p>

  <div class="abs card red" style="left:111px">
    <svg class="icon" width="86" height="86" viewBox="0 0 86 86"><circle cx="43" cy="43" r="42" fill="none" stroke="#fff" stroke-width="2" stroke-dasharray="6 4"/><circle cx="43" cy="43" r="34" fill="#fff"/><rect x="26" y="36" width="26" height="10" fill="#e8283c"/><rect x="52" y="39" width="9" height="7" fill="#e8283c"/><circle cx="32" cy="50" r="4" fill="#e8283c"/><circle cx="54" cy="50" r="4" fill="#e8283c"/></svg>
    <h3 class="display">Dirt</h3>
    <p>Sed ut perspiciatis unde omnis iste natus error sit voluptatem accusantium doloremque</p>
  </div>
  <div class="abs card teal" style="left:361px">
    <svg class="icon" width="86" height="86" viewBox="0 0 86 86"><circle cx="43" cy="43" r="42" fill="none" stroke="#fff" stroke-width="2" stroke-dasharray="6 4"/><circle cx="43" cy="43" r="34" fill="#fff"/><rect x="24" y="32" width="26" height="18" rx="3" fill="#1a6f96"/><rect x="50" y="38" width="11" height="12" fill="#1a6f96"/><circle cx="32" cy="53" r="4" fill="#1a6f96"/><circle cx="54" cy="53" r="4" fill="#1a6f96"/></svg>
    <h3 class="display">Gravel</h3>
    <p>Sed ut perspiciatis unde omnis iste natus error sit voluptatem accusantium doloremque</p>
  </div>
  <div class="abs card red" style="left:609px">
    <svg class="icon" width="86" height="86" viewBox="0 0 86 86"><circle cx="43" cy="43" r="42" fill="none" stroke="#fff" stroke-width="2" stroke-dasharray="6 4"/><circle cx="43" cy="43" r="34" fill="#fff"/><path d="M24 48 Q34 34 44 44 Q54 36 62 38 L62 48 Z" fill="#e8283c"/><rect x="24" y="51" width="38" height="3" fill="#e8283c"/></svg>
    <h3 class="display">Landscape Bark</h3>
    <p>Sed ut perspiciatis unde omnis iste natus error sit voluptatem accusantium doloremque</p>
  </div>
  <div class="abs card teal" style="left:859px">
    <svg class="icon" width="86" height="86" viewBox="0 0 86 86"><circle cx="43" cy="43" r="42" fill="none" stroke="#fff" stroke-width="2" stroke-dasharray="6 4"/><circle cx="43" cy="43" r="34" fill="#fff"/><polygon points="34,28 40,44 28,44" fill="#1a6f96"/><rect x="33" y="44" width="2" height="10" fill="#1a6f96"/><rect x="46" y="30" width="3" height="22" fill="#1a6f96"/><path d="M26 56 Q43 62 60 56" stroke="#1a6f96" stroke-width="3" fill="none"/></svg>
    <h3 class="display">Landscape Materials</h3>
    <p>Sed ut perspiciatis unde omnis iste natus error sit voluptatem accusantium doloremque</p>
  </div>

  <section class="about">
    <div class="abs about-band" role="img" aria-label="Faded photo of parked trucks"></div>
    <svg class="abs" style="top:1426px;left:525px" width="290" height="408" viewBox="0 0 290 408">
      <defs><linearGradient id="chev" x1="0" y1="0" x2="0" y2="1"><stop offset="0" stop-color="#f5304a"/><stop offset="1" stop-color="#dc2a22"/></linearGradient></defs>
      <polygon points="0,0 150,0 290,204 150,408 0,408 140,204" fill="url(#chev)"/>
    </svg>
    <div class="abs about-truck" role="img" aria-label="Blue semi truck cab"></div>
    <h2 class="abs display">About Us</h2>
    <p class="abs">Sed ut perspiciatis unde omnis iste natus error sit voluptatem accusantium doloremque laudantium, totam rem aperiam, eaque ipsa quae ab illo inventore veritatis et quasi architecto beatae vitae dicta sunt explicabo. Nemo enim ipsam voluptatem quia voluptas sit aspernatur aut odit aut fugit, sed quia consequuntur magni dolores eos qui ratione voluptatem sequi nesciunt.</p>
    <div class="btn" style="top:1725px;left:111px;width:127px;height:43px">Read More</div>
  </section>

  <h2 class="abs display sec-title" style="top:1985px">Get In Touch <span>With Us</span></h2>
  <p class="abs sec-text" style="top:2062px">Sed ut perspiciatis unde omnis iste natus error sit voluptatem accusantium doloremque laudantium, totam rem aperiam, eaque ipsa quae ab illo inventore veritatis et quasi architecto beatae vitae dicta sunt explicabo. Nemo enim ipsam voluptatem quia</p>

  <div class="abs info" style="top:2183px">
    <div class="ring"><svg width="14" height="18" viewBox="0 0 14 18"><path d="M7 0C3 0 0 3 0 7c0 5 7 11 7 11s7-6 7-11C14 3 11 0 7 0z" fill="var(--blue)"/><circle cx="7" cy="7" r="2.5" fill="#fff"/></svg></div>
    <div><h4>Location</h4><div class="txt">22 Quarry Lane, Lorem<br>Vale 540 118</div></div>
  </div>
  <div class="abs info" style="top:2288px">
    <div class="ring"><svg width="16" height="16" viewBox="0 0 24 24"><path d="M6.6 10.8a15 15 0 006.6 6.6l2.2-2.2c.3-.3.7-.4 1-.2 1.1.4 2.3.6 3.6.6.6 0 1 .4 1 1V20c0 .6-.4 1-1 1A17 17 0 013 4c0-.6.4-1 1-1h3.5c.6 0 1 .4 1 1 0 1.3.2 2.5.6 3.6.1.3 0 .7-.2 1z" fill="var(--blue)"/></svg></div>
    <div><h4>Phone</h4><div class="txt">+1 555 014 2290</div></div>
  </div>
  <div class="abs info" style="top:2371px">
    <div class="ring"><svg width="16" height="12" viewBox="0 0 16 12"><rect width="16" height="12" rx="1" fill="var(--blue)"/><path d="M1 1l7 6 7-6" stroke="#fff" stroke-width="1.5" fill="none"/></svg></div>
    <div><h4>Email</h4><div class="txt">hello@ridgelinehaul.example</div></div>
  </div>

  <div class="field" style="top:2175px;left:442px;width:318px;height:53px">Name</div>
  <div class="field" style="top:2243px;left:442px;width:318px;height:53px">Phone</div>
  <div class="field" style="top:2311px;left:442px;width:318px;height:53px">Email</div>
  <div class="btn" style="top:2381px;left:442px;width:318px;height:53px;font-size:17px">Submit</div>
  <div class="field" style="top:2175px;left:780px;width:300px;height:259px">Type your message</div>

  <footer class="abs footer">
    <div class="abs brand" style="top:70px;left:0;width:1200px;justify-content:center;font-size:28px"><span>RIDGELINE HAULAGE</span><span class="brand-square"></span></div>
    <nav class="abs footer-nav"><span>Home</span><span>|</span><span>About Us</span><span>|</span><span>Services</span><span>|</span><span>Contact Us</span></nav>
    <div class="abs social"><span></span><span></span><span></span></div>
    <p class="abs copy">© Copyright 2023 | All Rights Reserved.</p>
  </footer>

</div>
</body>
</html>
```